Business Cards Needed for Innovative Healthcare Marketing Company

We are a marketing company focused on healthcare. Our company is all about rebranding yourself renewing your image and generating results. The phoenix stands for "reborn" or "rising" which we provide new brands for our clients we take their old brands and renew it with creativity and innovation. I am looking for a business card with color dimension. I have attached an example of a card I think has the look and feel of what I am trying to accomplish. I like that the card example has black and grey font colors, I like the font placement and the small logo, I really like the use of the colors on the right those are the colors of my logo. My logo is phoenix so maybe incorporating flames similar to that design. I would like the back a solid color maybe red with an opaque version of the logo and website. As a marketing company I am always open to creative liberty!

Target Market(s)

Doctors and business professionals.

Industry/Entity Type

Marketing

Contact Information for Business Card

Valcorne Health Care Marketing
Marla Tenwick- CEO
#(512)638-2974
email-marla@valcorne.com
website- valcorne.com

Font styles to use
Sans Serif

Colors
ec1f27
f37122
ffc214
fbed22
fbf289
f04a50

Requirements
Must have
• The logo and required information
Nice to have
• icons by the information
Should not have
• child like font

```html
<!DOCTYPE html>
<html lang="en">
<head>
<meta charset="utf-8">
<title>Valcorne Health Care Marketing – Business Card</title>
<link href="https://fonts.googleapis.com/css2?family=Josefin+Sans:wght@300&family=Open+Sans:wght@400;600&display=swap" rel="stylesheet">
<style>
  :root {
    --stage: #ecebe9;
    --card-red: #a01d21;
    --brand-red: #a3222a;
    --flame-dark: #b8262a;
    --flame-mid: #e0532a;
    --flame-light: #f7a12a;
    --brand-orange: #f37122;
    --paper: #ffffff;
    --ink-light: #ffffff;
    --rule-light: rgba(255,255,255,0.75);
  }
  * { box-sizing: border-box; margin: 0; padding: 0; }
  html, body { width: 1200px; height: 900px; overflow: hidden; }
  body { background: var(--stage); position: relative; font-family: "Open Sans", sans-serif; }

  .card { position: absolute; box-shadow: 0 6px 18px rgba(0,0,0,0.18); overflow: hidden; }

  /* Front */
  .card--front { left: 238px; top: 62px; width: 555px; height: 342px; background: var(--paper); }
  .front-panel { position: absolute; left: 0; top: 0; width: 350px; height: 100%; background: var(--card-red); color: var(--ink-light); }
  .front-feature { position: absolute; left: 330px; top: 0; width: 225px; height: 100%; background: var(--paper); }
  .front-illustration {
    position: absolute; left: 262px; top: 0; width: 293px; height: 342px;
    background: linear-gradient(180deg, var(--flame-dark) 0%, var(--flame-mid) 50%, var(--flame-light) 100%);
    border-radius: 48% 48% 46% 46% / 30% 30% 70% 70%;
    border: 6px solid var(--paper);
  }

  .brand { position: absolute; left: 34px; top: 40px; width: 194px; }
  .brand__name { font-family: "Josefin Sans", sans-serif; font-weight: 300; font-size: 37px; line-height: 1; letter-spacing: 0.5px; white-space: nowrap; }
  .brand__rule { height: 1px; margin: 8px 0 5px; }
  .brand__tagline { font-family: "Josefin Sans", sans-serif; font-weight: 300; font-size: 13px; letter-spacing: 0.5px; white-space: nowrap; }
  .card--front .brand__rule { background: var(--rule-light); }

  .person { position: absolute; left: 34px; top: 158px; }
  .person__name { font-weight: 600; font-size: 20px; line-height: 1.1; }
  .person__role { font-size: 15px; margin-top: 2px; }

  .contact { position: absolute; left: 36px; top: 234px; list-style: none; }
  .contact__item { display: flex; align-items: center; font-size: 16px; height: 23px; }
  .contact__icon { width: 12px; height: 12px; margin-right: 9px; fill: var(--ink-light); }

  /* Back */
  .card--back { left: 457px; top: 519px; width: 560px; height: 342px; background: var(--paper); }
  .back-lockup { position: absolute; left: 148px; top: 112px; display: flex; align-items: center; }
  .back-lockup__mark { width: 100px; height: 100px; border-radius: 50%; background: var(--brand-orange); margin-right: 10px; }
  .card--back .brand { position: static; width: 170px; color: var(--brand-red); margin-top: 36px; }
  .card--back .brand__name { font-size: 31px; }
  .card--back .brand__rule { background: var(--brand-red); opacity: 0.6; margin: 6px 0 4px; }
  .card--back .brand__tagline { font-size: 12px; }
</style>
</head>
<body>

<section class="card card--front" aria-label="Business card front">
  <div class="front-feature"></div>
  <div class="front-panel">
    <div class="brand">
      <div class="brand__name">VALCORNE</div>
      <div class="brand__rule"></div>
      <div class="brand__tagline">HEALTH CARE MARKETING</div>
    </div>
    <div class="person">
      <div class="person__name">Marla Tenwick</div>
      <div class="person__role">CEO</div>
    </div>
    <ul class="contact">
      <li class="contact__item">
        <svg class="contact__icon" viewBox="0 0 24 24"><path d="M6.6 10.8a15.1 15.1 0 0 0 6.6 6.6l2.2-2.2a1 1 0 0 1 1-.25 11.4 11.4 0 0 0 3.6.57 1 1 0 0 1 1 1V20a1 1 0 0 1-1 1A17 17 0 0 1 3 4a1 1 0 0 1 1-1h3.5a1 1 0 0 1 1 1c0 1.25.2 2.45.57 3.57a1 1 0 0 1-.25 1z"/></svg>
        (512)638-2974
      </li>
      <li class="contact__item">
        <svg class="contact__icon" viewBox="0 0 24 24"><path d="M2 5h20v2l-10 7L2 7z"/><path d="M2 9l10 7 10-7v10H2z"/></svg>
        marla@valcorne.com
      </li>
      <li class="contact__item">
        <svg class="contact__icon" viewBox="0 0 24 24"><circle cx="12" cy="12" r="10"/><path d="M8 7l3 2-1 3 3 2v4M15 5l-1 3 3 2" fill="none" stroke="#a01d21" stroke-width="1.8"/></svg>
        valcorne.com
      </li>
    </ul>
  </div>
  <div class="front-illustration" role="img" aria-label="Large rising phoenix illustration with outspread wings in red fading to orange flames"></div>
</section>

<section class="card card--back" aria-label="Business card back">
  <div class="back-lockup">
    <div class="back-lockup__mark"></div>
    <div class="brand">
      <div class="brand__name">VALCORNE</div>
      <div class="brand__rule"></div>
      <div class="brand__tagline">HEALTH CARE MARKETING</div>
    </div>
  </div>
</section>

</body>
</html>
```